Poetry Book Cover Design Project

Looking for a minimalistic book cover design for a collection of poems. The book title is "Before The Lanterns Drift Away Slowly". There are three parts to the book. First covers poetry in the theme of Rage. Second love and desire. The third is strange poems. Essentially the sections are "Rage", "Desire" and the "Strange". The reason for the title "Before The Lanterns Drift Away Slowly" is as if someone is writing these till life changes towards the intended outcome as felt in each poem. I want to have the author's name "Ruvinath Kolongaswe" at the bottom. Ilustration attached.
- Minimalistic

```html
<!DOCTYPE html>
<html lang="en">
<head>
<meta charset="utf-8">
<title>Before The Lanterns Drift Away Slowly — Cover Series</title>
<link href="https://fonts.googleapis.com/css2?family=Tinos:wght@400;700&display=swap" rel="stylesheet">
<style>
  :root {
    --page: #ffffff;
    --ink-light: #fbf6ee;
    --glow: rgba(247, 210, 160, 0.38);
    --glow-fade: rgba(247, 210, 160, 0);
    --rage-a: #b8361a;
    --rage-b: #d1581f;
    --rage-c: #8e2412;
    --desire-a: #3a2d86;
    --desire-b: #6a2c7a;
    --desire-c: #2e2d7a;
    --strange-a: #5a2620;
    --strange-b: #2f4a4c;
    --strange-c: #7a2a22;
    --shadow: rgba(20, 10, 10, 0.55);
  }
  * { margin: 0; padding: 0; box-sizing: border-box; }
  html, body {
    width: 1200px; height: 726px; overflow: hidden;
    background: var(--page);
  }
  .series { position: relative; width: 1200px; height: 726px; }
  .cover {
    position: absolute; top: 75px; height: 551px;
    box-shadow: 9px 11px 10px var(--shadow);
    overflow: hidden;
    font-family: "Tinos", "Times New Roman", serif;
    color: var(--ink-light);
  }
  .cover--rage    { left: 16px;  width: 360px; }
  .cover--desire  { left: 422px; width: 368px; }
  .cover--strange { left: 825px; width: 355px; }

  .cover__art { position: absolute; inset: 0; }
  .cover--rage .cover__art {
    background:
      linear-gradient(155deg, transparent 0 20%, rgba(230,110,40,.35) 35%, transparent 50%, rgba(120,25,10,.35) 70%, transparent 85%),
      linear-gradient(160deg, var(--rage-c) 0%, var(--rage-a) 30%, var(--rage-b) 55%, var(--rage-a) 80%, var(--rage-c) 100%);
  }
  .cover--desire .cover__art {
    background:
      linear-gradient(90deg, transparent 0 30%, rgba(140,40,110,.45) 42%, transparent 55%, rgba(120,60,150,.4) 72%, transparent 85%),
      linear-gradient(180deg, var(--desire-b) 0%, var(--desire-a) 45%, var(--desire-c) 100%);
  }
  .cover--strange .cover__art {
    background:
      linear-gradient(170deg, transparent 0 25%, rgba(122,42,34,.55) 40%, transparent 55%, rgba(47,74,76,.6) 72%, transparent 88%),
      linear-gradient(180deg, var(--strange-a) 0%, var(--strange-b) 45%, var(--strange-c) 70%, var(--strange-b) 88%, var(--strange-c) 100%);
  }

  .cover__title {
    position: absolute; right: 40px; top: 86px;
    text-align: right; font-weight: 400;
    font-size: 48px; line-height: 51px;
  }
  .cover__title span { display: block; }
  .cover--desire .cover__title { right: 42px; }

  .cover__eyes {
    position: absolute; left: 0; right: 0; top: 422px; height: 40px;
    background:
      radial-gradient(ellipse 40px 18px at 27% 50%, var(--glow), var(--glow-fade)),
      radial-gradient(ellipse 40px 18px at 84% 50%, var(--glow), var(--glow-fade));
  }

  .cover__section {
    position: absolute; top: 476px; left: 0; right: 0;
    padding-left: 18px;
    text-align: center; font-size: 21px; letter-spacing: 0.5px; font-weight: 400;
  }
  .cover--desire .cover__section { font-weight: 700; }

  .cover__author {
    position: absolute; top: 503px; left: 0; right: 0;
    text-align: center; font-size: 16px; font-weight: 700;
  }
</style>
</head>
<body>
<main class="series">

  <article class="cover cover--rage">
    <div class="cover__art" role="img" aria-label="Marbled sandstone texture in flowing rust-red and orange streaks"></div>
    <h1 class="cover__title"><span>Before</span><span>The</span><span>Lanterns</span><span>Drift</span><span>Away</span><span>Slowly</span></h1>
    <div class="cover__eyes" role="img" aria-label="Two glowing crescent shapes like closed eyes"></div>
    <p class="cover__section">RAGE</p>
    <p class="cover__author">Ruvinath Kolongaswe</p>
  </article>

  <article class="cover cover--desire">
    <div class="cover__art" role="img" aria-label="Vertical painted texture in deep violet, indigo and magenta streaks"></div>
    <h1 class="cover__title"><span>Before</span><span>The</span><span>Lanterns</span><span>Drift</span><span>Away</span><span>Slowly</span></h1>
    <div class="cover__eyes" role="img" aria-label="Two glowing crescent shapes like closed eyes"></div>
    <p class="cover__section">DESIRE</p>
    <p class="cover__author">Ruvinath Kolongaswe</p>
  </article>

  <article class="cover cover--strange">
    <div class="cover__art" role="img" aria-label="Wavy marbled texture in dark red and teal bands"></div>
    <h1 class="cover__title"><span>Before</span><span>The</span><span>Lanterns</span><span>Drift</span><span>Away</span><span>Slowly</span></h1>
    <div class="cover__eyes" role="img" aria-label="Two glowing crescent shapes like closed eyes"></div>
    <p class="cover__section">STRANGE</p>
    <p class="cover__author">Ruvinath Kolongaswe</p>
  </article>

</main>
</body>
</html>
```